Business Card Design needed for start up company Halvora

In need of a new business card designed for a start up company based in Sydney, Halvora is a new start up innovative Company, our mission it to make property accessible for everyday Australian and to become the leading Real Estate platform in Australia. We want it to be fresh and clean.

Industry/Entity Type

Financial

Contact Information for Business Card

Section for Name
Section for Title

HALVORA - The Strength of Pooling
Mobile:
Direct:

Font styles to use
Sans Serif

Colors
33a6d7
0692cd
0255a3
ffffff

Requirements
Must have
• Logo, all business card details

```html
<!DOCTYPE html>
<html lang="en">
<head>
<meta charset="utf-8">
<title>Halvora Business Card</title>
<link href="https://fonts.googleapis.com/css2?family=Jost:wght@400;500;600&display=swap" rel="stylesheet">
<style>
  :root {
    --navy: #1f4079;
    --sky: #239bd8;
    --card-white: #f4f4f4;
    --ink: #4a4a4a;
    --backdrop: #e6e8ec;
    --white: #ffffff;
  }
  * { margin: 0; padding: 0; box-sizing: border-box; }
  html, body { width: 1200px; height: 960px; overflow: hidden; }
  body {
    position: relative;
    background: var(--backdrop);
    font-family: "Jost", sans-serif;
  }
  .card {
    position: absolute;
    width: 600px;
    height: 343px;
    border-radius: 18px;
    overflow: hidden;
    box-shadow: 0 3px 8px rgba(0,0,0,0.18);
  }
  .card-front { left: 216px; top: 131px; background: var(--card-white); }
  .card-back { left: 381px; top: 504px; background: var(--navy); }

  .brand-name {
    position: absolute;
    left: 0; right: 0;
    text-align: center;
    font-weight: 600;
    font-size: 56px;
    line-height: 1;
    letter-spacing: 2px;
  }
  .card-front .brand-name { top: 66px; color: var(--navy); }
  .card-back .brand-name { top: 144px; color: var(--white); }

  .divider {
    position: absolute;
    left: 44px; top: 170px;
    width: 512px; height: 1px;
    background: var(--navy);
  }
  .person { position: absolute; left: 44px; top: 186px; }
  .person-name {
    font-weight: 600; font-size: 21px; color: var(--navy);
    letter-spacing: 0.3px; line-height: 1.2;
  }
  .person-title {
    font-size: 15px; color: var(--sky); line-height: 1.3;
    margin-bottom: 5px;
  }
  .person-address {
    font-size: 14px; color: var(--ink); line-height: 1.35;
    font-style: normal;
  }
  .contacts {
    position: absolute; right: 43px; top: 193px;
    list-style: none;
  }
  .contacts li {
    display: flex; justify-content: flex-end; align-items: center;
    gap: 8px; font-size: 14px; color: var(--ink); height: 20px;
  }
  .contacts svg { width: 13px; height: 13px; flex: none; }
  .icon-fill { fill: var(--navy); }
  .icon-line { fill: none; stroke: var(--navy); stroke-width: 1.6; }

  .wave { position: absolute; left: 0; top: 0; width: 600px; height: 343px; }
  .tagline {
    position: absolute; left: 0; right: 0; bottom: 7px;
    text-align: center; color: var(--white);
    font-size: 14.5px; font-weight: 400;
  }
</style>
</head>
<body>

<section class="card card-front" aria-label="Card front">
  <svg class="wave" viewBox="0 0 600 343" aria-hidden="true">
    <path d="M0,272 Q220,312 420,309 Q520,306 600,296 L600,343 L0,343 Z" fill="var(--sky)"/>
    <path d="M0,280 Q230,314 430,311 Q525,308 600,293 L600,343 L0,343 Z" fill="var(--white)"/>
    <path d="M0,286 Q240,318 440,313 Q530,309 600,290 L600,343 L0,343 Z" fill="var(--navy)"/>
  </svg>

  <p class="brand-name">HALVORA</p>

  <div class="divider"></div>

  <div class="person">
    <h1 class="person-name">MAREN OSTBY</h1>
    <p class="person-title">CEO/FOUNDER</p>
    <address class="person-address">4120 Wattle Street<br>Sydney, NSW 2000</address>
  </div>

  <ul class="contacts">
    <li>612 408 3175
      <svg viewBox="0 0 16 16" aria-label="Direct"><path class="icon-fill" d="M3 1l3 3-2 2c1 2 3 4 5 5l2-2 3 3-2 3C6 14 2 10 1 3z"/></svg>
    </li>
    <li>614 752 0936
      <svg viewBox="0 0 16 16" aria-label="Mobile"><rect class="icon-line" x="4.5" y="1" width="7" height="14" rx="1"/><rect class="icon-fill" x="7" y="12" width="2" height="1.2"/></svg>
    </li>
    <li>maren@halvora.com
      <svg viewBox="0 0 16 16" aria-label="Email"><rect class="icon-fill" x="1" y="3.5" width="14" height="9"/><path d="M1.5 4l6.5 5 6.5-5" fill="none" stroke="var(--white)" stroke-width="1.2"/></svg>
    </li>
    <li>www.halvora.com
      <svg viewBox="0 0 16 16" aria-label="Web"><circle class="icon-fill" cx="8" cy="8" r="7"/><path d="M1.5 8h13M8 1.5c-3 3-3 10 0 13M8 1.5c3 3 3 10 0 13" fill="none" stroke="var(--white)" stroke-width="1"/></svg>
    </li>
  </ul>

  <p class="tagline">The Strength of Pooling</p>
</section>

<section class="card card-back" aria-label="Card back">
  <p class="brand-name">HALVORA</p>
</section>

</body>
</html>
```